Vernac Law Business cards and stationary design project

We are looking for a stationary design for business cards (double sided), 8x10, 5x7, and legal and standard envelopes.

We would like the design to match the logo that we have already.
Color palate preferred is Teal, White, grey and any others that will look good for a professional law firm.

We would like this statement: "INTEGRITY. DILIGENCE. ADVOCACY" to be on the back of the business cards and maybe on the stationary if it looks good.

Please see link to website for more information: www.vernac-law.example

Target Market(s)

Potential clients that need Attorney services.

Industry/Entity Type

Law Firm

Contact Information for Business Card

We would like the front and back to be two different colors. Current business cards are teal front, grey back and are a vertical design. We are open to options with colors.

Font styles to use
Serif

Colors
33a6d7
33b8a4
b9b9b9
5c5c5c

Requirements
Must have
• Logo supplied needs to go on the card and stationary.
• Match website color palate, www.vernac-law.example
• Be professional and not too wordy.
• Criminal Law, Civil Litigation, Personal Injury, Restraining Orders need to be on the card.
Nice to have
• RELATIONSHIPS. RESPECT. RESULTS. on the back of the card.
Should not have
• Not be too busy/wordy or too flashy.

```html
<!DOCTYPE html>
<html lang="en">
<head>
<meta charset="utf-8">
<title>Vernac Law – Business Card</title>
<link rel="stylesheet" href="https://fonts.googleapis.com/css2?family=PT+Sans:wght@400;700&display=swap">
<style>
  :root {
    --page: #dcdcdc;
    --ink: #060606;
    --teal: #10889a;
    --white: #ffffff;
    --shadow: rgba(0, 0, 0, 0.25);
  }
  html, body {
    margin: 0;
    padding: 0;
    width: 1200px;
    height: 900px;
    overflow: hidden;
    background: var(--page);
    font-family: "PT Sans", Arial, sans-serif;
  }
  .canvas {
    position: relative;
    width: 1200px;
    height: 900px;
  }
  .card {
    position: absolute;
    left: 250px;
    width: 700px;
    height: 400px;
    overflow: hidden;
    box-shadow: 0 6px 18px var(--shadow);
  }

  /* Card back: black with practice areas */
  .card-back {
    top: 35px;
    background: var(--ink);
    color: var(--teal);
    text-align: center;
  }
  .firm-name {
    position: absolute;
    top: 88px;
    left: 0;
    right: 0;
    margin: 0;
    font-size: 48px;
    font-weight: 700;
    letter-spacing: 4px;
    line-height: 1;
  }
  .firm-suffix {
    position: absolute;
    top: 150px;
    left: 0;
    right: 0;
    display: flex;
    justify-content: center;
    align-items: center;
    gap: 14px;
    font-size: 12px;
    line-height: 1;
  }
  .firm-suffix span {
    letter-spacing: 8px;
    padding-left: 8px;
  }
  .firm-suffix::before,
  .firm-suffix::after {
    content: "";
    width: 70px;
    height: 1px;
    background: var(--teal);
  }
  .practice {
    position: absolute;
    top: 190px;
    left: 0;
    right: 0;
    margin: 0;
    font-size: 19px;
    line-height: 1.35;
  }
  .tagline-row {
    position: absolute;
    top: 262px;
    left: 0;
    right: 0;
    display: flex;
    align-items: center;
    gap: 18px;
  }
  .tagline-row::before,
  .tagline-row::after {
    content: "";
    flex: 1;
    height: 2px;
    background: var(--teal);
  }
  .tagline {
    margin: 0;
    font-size: 19px;
    font-weight: 700;
    letter-spacing: 0.5px;
    line-height: 1;
  }

  /* Card front: black and teal with contacts */
  .card-front {
    top: 465px;
    background: var(--teal);
  }
  .card-front .shape {
    position: absolute;
    inset: 0;
  }
  .front-name {
    position: absolute;
    left: 40px;
    top: 150px;
    width: 240px;
    margin: 0;
    text-align: center;
    color: var(--teal);
    font-size: 46px;
    font-weight: 700;
    line-height: 1;
  }
  .contact-block {
    position: absolute;
    right: 36px;
    top: 42px;
    text-align: right;
    color: var(--white);
  }
  .person-name {
    margin: 0;
    font-size: 24px;
    font-weight: 700;
    line-height: 1.2;
  }
  .person-title {
    margin: 0 0 20px;
    font-size: 19px;
    line-height: 1.3;
  }
  .contact-list {
    list-style: none;
    margin: 0;
    padding: 0;
    font-size: 19px;
    line-height: 1.3;
  }
  .contact-list li {
    display: flex;
    justify-content: flex-end;
    align-items: center;
    gap: 10px;
  }
  .contact-list .address {
    margin-top: 12px;
  }
  .address-text {
    display: block;
  }
  .icon {
    width: 14px;
    height: 14px;
    flex: none;
  }
</style>
</head>
<body>
<main class="canvas">

  <section class="card card-back" aria-label="Business card back">
    <h1 class="firm-name">VERNAC LAW</h1>
    <div class="firm-suffix"><span>APC</span></div>
    <p class="practice">Practice areas, Criminal Law<br>Civil Litigation/Personal Injury, Restraining Orders</p>
    <div class="tagline-row">
      <p class="tagline">INTEGRITY. DILIGENCE. ADVOCACY</p>
    </div>
  </section>

  <section class="card card-front" aria-label="Business card front">
    <svg class="shape" width="700" height="400" viewBox="0 0 700 400" aria-hidden="true">
      <path d="M0,0 H300 C385,70 375,300 225,400 H0 Z" fill="#060606"/>
      <path d="M318,0 C400,85 380,300 248,400" fill="none" stroke="#060606" stroke-width="3"/>
    </svg>
    <p class="front-name">Vernac<br>Law</p>
    <div class="contact-block">
      <p class="person-name">Daniel Marsh</p>
      <p class="person-title">Managing Director</p>
      <ul class="contact-list">
        <li>123.456.7890
          <svg class="icon" viewBox="0 0 16 16" aria-hidden="true"><path fill="#fff" d="M1 6c0-3 14-3 14 0v2h-4V6H5v2H1z M3 9h10l1 5H2z"/></svg>
        </li>
        <li>123.456.7890
          <svg class="icon" viewBox="0 0 16 16" aria-hidden="true"><rect x="3" y="1" width="10" height="5" fill="#fff"/><rect x="1" y="6" width="14" height="9" rx="1" fill="#fff"/><rect x="4" y="9" width="8" height="3" fill="#10889a"/></svg>
        </li>
        <li>info@youremail.com
          <svg class="icon" viewBox="0 0 16 16" aria-hidden="true"><rect x="1" y="3" width="14" height="10" fill="#fff"/><path d="M1 3l7 6 7-6" fill="none" stroke="#10889a" stroke-width="1.5"/></svg>
        </li>
        <li>www.website.com
          <svg class="icon" viewBox="0 0 16 16" aria-hidden="true"><g fill="none" stroke="#fff" stroke-width="2"><rect x="1" y="7" width="8" height="5" rx="2.5" transform="rotate(-45 5 9.5)"/><rect x="7" y="4" width="8" height="5" rx="2.5" transform="rotate(-45 11 6.5)"/></g></svg>
        </li>
        <li class="address">
          <span class="address-text">1234, Address Goes Here<br>Country Name, 123456</span>
          <svg class="icon" viewBox="0 0 16 16" aria-hidden="true"><path fill="#fff" d="M8 1a5 5 0 0 1 5 5c0 4-5 9-5 9S3 10 3 6a5 5 0 0 1 5-5z"/><circle cx="8" cy="6" r="2" fill="#10889a"/></svg>
        </li>
      </ul>
    </div>
  </section>

</main>
</body>
</html>
```